Business Card Design for Training Business

Clear Path Coaching is a new business that delivers training and other services with a focus on topics related to mental health and wellbeing, for example, Wellmind Response Course, Resilience etc. We have a strong focus on evidence-based psychology and neuroscience. I have a logo which I will upload with the brief, so please consider colours that work well with the logo.
Target Market(s)
Adults, workplaces (particularly government and not-for-profits)
Industry/Entity Type
Business
Contact Information for Business Card
Head Strong TrainingSamantha SellwoodDirector0438 770 850sam@headstrongtraining.com.auwww.headstrongtraining.com.au

```html
<!DOCTYPE html>
<html lang="en">
<head>
<meta charset="utf-8">
<title>Clear Path Coaching – Business Card</title>
<link rel="stylesheet" href="https://fonts.googleapis.com/css2?family=Raleway:wght@300&family=Lato:wght@700&family=Arimo:wght@400&display=swap">
<style>
  :root {
    --backdrop: #3a3a3c;
    --card: #fbfbfb;
    --card-line: rgba(0, 0, 0, 0.025);
    --teal: #2fb3b6;
    --teal-soft: #5cc6c4;
    --ink: #4a4a4c;
    --ink-soft: #77787a;
  }
  * { margin: 0; padding: 0; box-sizing: border-box; }
  html, body {
    width: 1200px;
    height: 857px;
    overflow: hidden;
    background: var(--backdrop);
  }
  .card {
    position: absolute;
    left: 75px;
    top: 128px;
    width: 1050px;
    height: 600px;
    background-color: var(--card);
    background-image: repeating-linear-gradient(-30deg, var(--card-line) 0 1px, transparent 1px 5px);
    box-shadow: 0 10px 30px rgba(0, 0, 0, 0.45);
  }
  .brand {
    position: absolute;
    left: 0;
    right: 0;
    top: 70px;
    display: flex;
    flex-direction: column;
    align-items: center;
    gap: 34px;
  }
  .brand-dot {
    width: 120px;
    height: 120px;
    border: 3px solid var(--teal);
    border-radius: 50%;
  }
  .brand-name {
    font-family: "Raleway", sans-serif;
    font-weight: 300;
    font-size: 44px;
    letter-spacing: 0.14em;
    text-transform: uppercase;
    color: var(--ink);
  }
  .person {
    position: absolute;
    left: 70px;
    bottom: 70px;
    font-family: "Arimo", sans-serif;
  }
  .person-name {
    font-size: 40px;
    color: var(--teal-soft);
    text-transform: uppercase;
    letter-spacing: -0.01em;
  }
  .person-role {
    font-size: 36px;
    color: var(--ink-soft);
    margin-top: 4px;
  }
  .contact {
    position: absolute;
    right: 60px;
    top: 345px;
    list-style: none;
    font-family: "Lato", sans-serif;
    font-weight: 700;
    font-size: 25px;
    color: var(--ink);
  }
  .contact-item {
    display: flex;
    align-items: center;
    gap: 18px;
    margin-bottom: 20px;
  }
  .contact-icon {
    width: 30px;
    height: 26px;
    flex: none;
    fill: var(--teal);
  }
</style>
</head>
<body>
  <main class="card">
    <header class="brand">
      <div class="brand-dot"></div>
      <div class="brand-name">Clear Path Coaching</div>
    </header>

    <section class="person">
      <div class="person-name">Rebecca Tanfield</div>
      <div class="person-role">Director</div>
    </section>

    <ul class="contact">
      <li class="contact-item">
        <svg class="contact-icon" viewBox="0 0 30 26" aria-hidden="true">
          <path d="M2 8 Q15 0 28 8 L28 11 L21 11 L21 8 Q15 6 9 8 L9 11 L2 11 Z"/>
          <path d="M8 12 L22 12 L27 24 L3 24 Z"/>
        </svg>
        <span>0491 362 517</span>
      </li>
      <li class="contact-item">
        <svg class="contact-icon" viewBox="0 0 30 26" aria-hidden="true">
          <rect x="1" y="4" width="28" height="19"/>
          <path d="M1 4 L15 15 L29 4" fill="none" stroke="#fbfbfb" stroke-width="2"/>
        </svg>
        <span>bec@clearpathcoaching.example.au</span>
      </li>
      <li class="contact-item">
        <svg class="contact-icon" viewBox="0 0 30 26" aria-hidden="true">
          <g fill="none" stroke="#2fb3b6" stroke-width="3.5" stroke-linecap="round">
            <path d="M13 9 L18 4 Q21 1 24 4 Q27 7 24 10 L19 15"/>
            <path d="M17 17 L12 22 Q9 25 6 22 Q3 19 6 16 L11 11"/>
          </g>
        </svg>
        <span>www.clearpathcoaching.example.au</span>
      </li>
    </ul>
  </main>
</body>
</html>
```